Beacon Advisory Website

I currently have a website www.beaconadvisoryinc.com. We are a IT Consulting Company. Our website will pretty much tell out our services. I am looking to enhance my website and make it look more professional. Looking for very classy and Contemporary look and design for my website.

It Company

```html
<!DOCTYPE html>
<html lang="en">
<head>
<meta charset="utf-8">
<title>Beacon Advisory</title>
<link rel="stylesheet" href="https://fonts.googleapis.com/css2?family=Bebas+Neue&family=Roboto:wght@300;400;500;700&display=swap">
<style>
:root{
  --blue:#1b62ad;
  --blue-dark:#154f8d;
  --ink:#222;
  --text:#555;
  --muted:#888;
  --line:#dcdcdc;
  --soft:#f4f4f4;
  --dark:#25282b;
  --darker:#141516;
  --white:#fff;
}
*{box-sizing:border-box;margin:0;padding:0}
html,body{width:1200px;height:3947px;overflow:hidden}
body{font-family:"Roboto",Arial,sans-serif;color:var(--text);background:var(--white);position:relative}
.abs{position:absolute}

/* header */
.site-header{position:absolute;left:0;top:0;width:1200px;height:116px;background:var(--white);box-shadow:0 2px 6px rgba(0,0,0,.08);z-index:2}
.brand{position:absolute;left:79px;top:20px;display:flex;align-items:center;gap:12px}
.brand-mark{width:58px;height:58px;background:var(--blue);border-radius:50%}
.brand-name{font-size:34px;font-weight:700;color:var(--ink);letter-spacing:1px;line-height:1}
.brand-name small{display:block;font-size:15px;font-weight:400;color:var(--blue);letter-spacing:3px;margin-top:4px}
.main-nav{position:absolute;right:76px;top:37px;display:flex}
.main-nav a{display:block;height:45px;line-height:45px;padding:0 17px;font-size:17px;color:var(--ink);text-decoration:none;text-transform:uppercase}
.main-nav a.active{background:var(--blue);color:var(--white)}

/* hero */
.hero{position:absolute;left:0;top:116px;width:1200px;height:679px;background:linear-gradient(90deg,#c9ced4 0%,#e4e4e2 40%,#e9e4dc 70%,#cdb9a0 100%)}
.hero-title{position:absolute;left:79px;top:180px;font-family:"Bebas Neue",Impact,sans-serif;font-size:72px;color:#111;letter-spacing:2px;line-height:1}
.hero-sub{position:absolute;left:79px;top:266px;width:560px;font-size:28px;font-weight:700;color:#111;line-height:1.25}
.hero-btn{position:absolute;left:79px;top:352px;width:187px;height:64px;border:2px solid #222;font-size:20px;color:#111;line-height:60px;text-align:center;text-transform:uppercase}

/* features */
.feature{position:absolute;top:855px;width:340px;text-align:center}
.feature-icon{width:124px;height:124px;margin:0 auto;border-radius:50%;border:2px solid #e3e3e3;display:flex;align-items:center;justify-content:center}
.feature-icon span{width:104px;height:104px;border-radius:50%;background:#f1f1f1;display:flex;align-items:center;justify-content:center}
.feature-icon.on span{background:var(--blue)}
.feature h3{margin-top:30px;font-size:21px;font-weight:500;color:var(--ink);text-transform:uppercase}
.feature p{margin-top:14px;font-size:14px;line-height:24px;color:var(--text)}
.feature p b{font-weight:400;color:var(--blue)}

/* welcome */
.welcome{position:absolute;left:0;top:1190px;width:1200px;height:329px;background:var(--soft)}
.eyebrow{font-size:21px;color:var(--blue);text-transform:uppercase}
.section-title{font-size:43px;font-weight:400;color:var(--blue);text-transform:uppercase;line-height:1.1}
.welcome p{position:absolute;left:79px;top:162px;width:660px;font-size:15px;line-height:24px;color:#333}
.btn-outline,.btn-solid{position:absolute;top:189px;width:163px;height:63px;font-size:20px;line-height:59px;text-align:center;text-transform:uppercase}
.btn-outline{left:787px;border:2px solid var(--blue);color:var(--blue)}
.btn-solid{left:961px;background:var(--blue);color:var(--white);border:2px solid var(--blue)}

.rule{position:absolute;left:79px;width:1045px;height:1px;background:var(--line)}

/* solutions */
.solution{position:absolute;top:1653px;width:337px}
.solution-media{width:337px;height:224px;border:3px solid #333}
.solution h3{margin-top:28px;font-size:21px;font-weight:400;color:var(--blue);text-transform:uppercase}
.solution p{margin-top:12px;font-size:14px;line-height:22px;color:var(--text);white-space:nowrap;overflow:hidden;text-overflow:ellipsis}
.read-more{margin-top:18px;font-size:15px;color:var(--text);text-transform:uppercase;display:flex;align-items:center;gap:8px}
.read-more.blue{color:var(--blue)}

/* career */
.career{position:absolute;left:0;top:2100px;width:1200px;height:208px;background:linear-gradient(90deg,#2e3235 0%,#3c3f42 50%,#2a2c2e 100%);color:var(--white)}
.career h2{position:absolute;left:79px;top:48px;font-size:43px;font-weight:400;text-transform:uppercase}
.career p{position:absolute;left:79px;top:104px;width:700px;font-size:16px;line-height:26px}
.career .mail{position:absolute;right:76px;top:122px;font-size:22px}

/* services */
.service{position:absolute;width:320px;height:105px}
.service-icon{position:absolute;left:0;top:0;width:105px;height:105px;border:2px solid var(--blue);border-radius:8px;display:flex;align-items:center;justify-content:center;background:var(--white)}
.service-icon.on{background:var(--blue)}
.service h3{position:absolute;left:121px;top:6px;font-size:17px;font-weight:400;color:var(--blue);text-transform:uppercase;line-height:1.15}
.service p{position:absolute;left:121px;width:200px;font-size:13.5px;line-height:23px;color:var(--text)}

/* testimonial */
.testimonial{position:absolute;left:0;top:2841px;width:1200px;height:365px;background:var(--soft)}
.quote-mark{position:absolute;left:132px;top:10px;font-family:Georgia,serif;font-size:260px;line-height:1;color:#d2d2d2}
.client-photo{position:absolute;left:268px;top:112px;width:106px;height:106px;border:3px solid var(--blue);background:linear-gradient(160deg,#cfd8e2,#8fa2b6)}
.testimonial p{position:absolute;left:395px;top:118px;width:729px;font-size:15px;line-height:28px;color:#333}
.client-name{position:absolute;left:395px;top:200px;font-size:16px;color:var(--blue);text-transform:uppercase}
.pager{position:absolute;top:259px;width:39px;height:39px;border:2px solid #666;display:flex;align-items:center;justify-content:center}

/* clients */
.clients-title{position:absolute;left:0;top:3262px;width:1200px;text-align:center;font-size:43px;color:var(--blue);text-transform:uppercase}
.client-logo{position:absolute;top:3343px;width:168px;height:84px;border:2px solid #ccc;border-radius:6px;box-shadow:0 2px 4px rgba(0,0,0,.12);display:flex;align-items:center;justify-content:center;font-size:21px;font-weight:700;color:#333;background:var(--white)}

/* footer */
.site-footer{position:absolute;left:0;top:3495px;width:1200px;height:390px;background:linear-gradient(120deg,#2b2e31 0%,#34373a 55%,#222426 100%);color:var(--white)}
.footer-col{position:absolute;top:62px}
.footer-col h4{font-size:18px;font-weight:400;text-transform:uppercase;letter-spacing:.5px}
.footer-col ul{list-style:none;margin-top:42px}
.footer-col li{font-size:14px;line-height:33px;text-transform:uppercase}
.footer-col .addr{font-size:14px;line-height:22px;margin:12px 0 16px 20px;text-transform:none}
.footer-col .addr span{color:#4d8fd6}
.social{display:flex;gap:10px;margin-top:42px}
.social i{width:52px;height:52px;border:2px solid #888;display:flex;align-items:center;justify-content:center}
.social i:first-child{background:var(--white)}
.social i b{width:18px;height:18px;border-radius:50%;background:var(--blue)}
.newsletter p{margin-top:42px;font-size:14px;line-height:24px;width:240px}
.email-field{margin-top:20px;width:218px;height:42px;border:1px solid #999;font-size:14px;line-height:40px;padding-left:12px}
.subscribe{margin-top:14px;width:157px;height:53px;background:var(--white);color:var(--blue);font-size:20px;line-height:53px;text-align:center;text-transform:uppercase}
.copyright{position:absolute;left:0;top:3885px;width:1200px;height:62px;background:var(--darker);color:var(--white);font-size:14px;text-align:center;line-height:62px}
.copyright span{color:#4d8fd6}
</style>
</head>
<body>

<header class="site-header">
  <div class="brand">
    <div class="brand-mark"></div>
    <div class="brand-name">BEACON<small>ADVISORY</small></div>
  </div>
  <nav class="main-nav">
    <a class="active">Company</a><a>Services</a><a>Solution</a><a>Resources</a><a>Career</a><a>Contact Us</a>
  </nav>
</header>

<section class="hero" role="img" aria-label="Smiling businesswoman in a suit in a bright office with colleagues blurred behind">
  <h1 class="hero-title">Beacon Advisory</h1>
  <p class="hero-sub">We provide unique and tailored solutions for various industries!</p>
  <div class="hero-btn">Contact Now</div>
</section>

<section class="features">
  <div class="feature" style="left:67px">
    <div class="feature-icon on"><span>
      <svg width="50" height="40" viewBox="0 0 50 40" fill="none" stroke="#fff" stroke-width="2.5"><circle cx="12" cy="10" r="5"/><circle cx="25" cy="8" r="5"/><circle cx="38" cy="10" r="5"/><path d="M4 30v-6a8 8 0 0 1 16 0M17 28v-6a8 8 0 0 1 16 0M30 30v-6a8 8 0 0 1 16 0M2 34h46"/></svg>
    </span></div>
    <h3>Consulting</h3>
    <p>Beacon Advisory has certified professional consultants to work with you to help increase the business by ... <b>READ MORE</b></p>
  </div>
  <div class="feature" style="left:430px">
    <div class="feature-icon"><span>
      <svg width="44" height="40" viewBox="0 0 44 40" fill="none" stroke="#777" stroke-width="2"><circle cx="22" cy="9" r="5"/><circle cx="10" cy="14" r="4"/><circle cx="34" cy="14" r="4"/><path d="M13 32v-8a9 9 0 0 1 18 0v8M3 32v-6a7 7 0 0 1 9-6M41 32v-6a7 7 0 0 0-9-6"/></svg>
    </span></div>
    <h3>Staff Augmentation</h3>
    <p>For years Beacon Advisory as been offering our customers the ability to augment their existing staff ...<b>READ MORE</b></p>
  </div>
  <div class="feature" style="left:785px">
    <div class="feature-icon"><span>
      <svg width="36" height="44" viewBox="0 0 36 44" fill="none" stroke="#777" stroke-width="2"><path d="M18 6a11 11 0 0 0-7 19c2 2 3 4 3 6h8c0-2 1-4 3-6a11 11 0 0 0-7-19z"/><path d="M14 35h8M15 39h6M18 0v2M4 6l2 2M32 6l-2 2M0 18h2M34 18h2"/></svg>
    </span></div>
    <h3>Offshore</h3>
    <p>Our Offshore development model has a unique distinction of providing efficient software solutions... <b>READ MORE</b></p>
  </div>
</section>

<section class="welcome">
  <div class="eyebrow abs" style="left:79px;top:64px">Welcome to</div>
  <h2 class="section-title abs" style="left:79px;top:100px">Beacon Advisory</h2>
  <p>Today's IT market is a dynamic, fast-paced industry, with ever-increasing demands. Meeting these demands for over 25 years, Beacon Advisory maintains a global presence, aggressively recruiting expertly qualified IT and Management Professionals from around the world and cultivating key partnerships with corporations to ...</p>
  <div class="btn-outline">Learn More</div>
  <div class="btn-solid">Join Us</div>
</section>

<div class="rule" style="top:1519px"></div>

<h2 class="section-title abs" style="left:79px;top:1574px">Our Solution</h2>

<article class="solution" style="left:79px">
  <div class="solution-media" role="img" aria-label="Dashboard software screenshots on a desktop and a smartphone" style="background:linear-gradient(135deg,#eef1f5,#cdd6df 60%,#3a3d42)"></div>
  <h3>Dashbord</h3>
  <p>Dashboards are a key component of every organization's Performance Management and...</p>
  <div class="read-more blue">Read More <svg width="30" height="10" viewBox="0 0 30 10"><path d="M0 5h27M23 1l4 4-4 4" stroke="#1b62ad" stroke-width="1.5" fill="none"/></svg></div>
</article>
<article class="solution" style="left:432px">
  <div class="solution-media" role="img" aria-label="Data warehouse diagram with linked database nodes" style="background:linear-gradient(135deg,#e8f1f9,#b9d3ea)"></div>
  <h3>Data Warehousing</h3>
  <p>A data warehouse is the concept of data extracted from operational systems and...</p>
  <div class="read-more">Read More <svg width="30" height="10" viewBox="0 0 30 10"><path d="M0 5h27M23 1l4 4-4 4" stroke="#555" stroke-width="1.5" fill="none"/></svg></div>
</article>
<article class="solution" style="left:787px">
  <div class="solution-media" role="img" aria-label="Colourful word cloud about business process with gears" style="background:linear-gradient(135deg,#fbeee0,#f2d6d6 50%,#d9e4f2)"></div>
  <h3>BPM</h3>
  <p>Beacon Advisory having Flowline Certified Consultants in to provide Business Process...</p>
  <div class="read-more">Read More <svg width="30" height="10" viewBox="0 0 30 10"><path d="M0 5h27M23 1l4 4-4 4" stroke="#555" stroke-width="1.5" fill="none"/></svg></div>
</article>

<section class="career" role="img" aria-label="Dark background of a business handshake">
  <h2>Career</h2>
  <p>To apply for a job, please mail your resume highlighting your qualifications.We would notify you via email when an opportunity arises that matches your profile.</p>
  <div class="mail">Mail id: careers@beaconadvisoryinc.com</div>
</section>

<div class="eyebrow abs" style="left:79px;top:2386px">Our</div>
<h2 class="section-title abs" style="left:79px;top:2418px">Services</h2>

<div class="service" style="left:79px;top:2506px">
  <div class="service-icon on"><svg width="46" height="52" viewBox="0 0 36 44" fill="none" stroke="#fff" stroke-width="2"><path d="M18 6a11 11 0 0 0-7 19c2 2 3 4 3 6h8c0-2 1-4 3-6a11 11 0 0 0-7-19z"/><path d="M14 35h8M15 39h6M18 0v2M4 6l2 2M32 6l-2 2M0 18h2M34 18h2"/></svg></div>
  <h3>Technology</h3><p style="top:30px">Beacon Advisory Training programs are perfect for individuals to enhance their...</p>
</div>
<div class="service" style="left:432px;top:2506px">
  <div class="service-icon"><svg width="50" height="46" viewBox="0 0 50 46" fill="#1b62ad"><rect x="4" y="30" width="7" height="14"/><rect x="15" y="24" width="7" height="20"/><rect x="26" y="18" width="7" height="26"/><rect x="37" y="10" width="7" height="34"/><path d="M4 22L18 10l10 6L42 2" stroke="#1b62ad" stroke-width="3" fill="none"/></svg></div>
  <h3>Business</h3><p style="top:30px">Beacon Advisory Training programs are perfect for individuals to enhance their...</p>
</div>
<div class="service" style="left:790px;top:2506px">
  <div class="service-icon"><svg width="44" height="50" viewBox="0 0 44 50" fill="none" stroke="#1b62ad" stroke-width="3"><rect x="4" y="6" width="30" height="40" rx="2"/><rect x="13" y="2" width="12" height="8"/><path d="M10 22l4 4 8-8M10 36h14"/><circle cx="36" cy="36" r="6"/></svg></div>
  <h3>IT Consulting</h3><p style="top:30px">Beacon Advisory Training programs are perfect for individuals to enhance their...</p>
</div>
<div class="service" style="left:79px;top:2663px">
  <div class="service-icon"><svg width="56" height="34" viewBox="0 0 56 34" fill="none" stroke="#1b62ad" stroke-width="3"><path d="M2 10l10-6 12 4 8-4 12 2 10 6M12 22l10 8 6-2 8 4 10-10M22 12l10 8"/></svg></div>
  <h3>Enterprise<br>Integration</h3><p style="top:52px">Beacon Advisory Training programs are perfect for ...</p>
</div>
<div class="service" style="left:432px;top:2663px">
  <div class="service-icon"><svg width="46" height="46" viewBox="0 0 46 46" fill="#1b62ad"><rect x="0" y="0" width="12" height="12"/><rect x="17" y="0" width="12" height="12"/><rect x="34" y="0" width="12" height="12"/><rect x="0" y="17" width="12" height="12"/><rect x="17" y="17" width="12" height="12"/><rect x="34" y="17" width="12" height="12"/><rect x="0" y="34" width="12" height="12"/><rect x="17" y="34" width="12" height="12"/><rect x="34" y="34" width="12" height="12"/></svg></div>
  <h3>Application</h3><p style="top:30px">Beacon Advisory Training programs are perfect for individuals to enhance their...</p>
</div>
<div class="service" style="left:790px;top:2663px">
  <div class="service-icon"><svg width="50" height="50" viewBox="0 0 50 50" fill="#1b62ad"><circle cx="20" cy="30" r="13"/><circle cx="20" cy="30" r="5" fill="#fff"/><circle cx="38" cy="12" r="9"/><circle cx="38" cy="12" r="3.5" fill="#fff"/><g stroke="#1b62ad" stroke-width="5"><path d="M20 12v6M20 42v6M2 30h6M32 30h6M7 17l4 4M29 39l4 4M7 43l4-4M29 21l4-4"/></g></svg></div>
  <h3>Development</h3><p style="top:30px">Beacon Advisory Training programs are perfect for individuals to enhance their...</p>
</div>

<section class="testimonial">
  <div class="rule" style="top:0;left:79px"></div>
  <div class="quote-mark">&ldquo;</div>
  <div class="client-photo" role="img" aria-label="Client portrait"></div>
  <p>Lorem Ipsum is simply dummy text of the printing and typesetting industry. Lorem Ipsum has been the industry's standard dummy text ever since the 1500s, when an unknown printer took a galley of type and scrambled it to make a type specimen book....</p>
  <div class="client-name">Client Name</div>
  <div class="pager" style="left:547px"><svg width="16" height="14" viewBox="0 0 16 14" fill="none" stroke="#555" stroke-width="2"><path d="M8 1L2 7l6 6M14 1L8 7l6 6"/></svg></div>
  <div class="pager" style="left:605px"><svg width="16" height="14" viewBox="0 0 16 14" fill="none" stroke="#555" stroke-width="2"><path d="M2 1l6 6-6 6M8 1l6 6-6 6"/></svg></div>
</section>

<h2 class="clients-title">Our Clients</h2>
<div class="client-logo" style="left:79px">BOLTLINE</div>
<div class="client-logo" style="left:290px">Restwell</div>
<div class="client-logo" style="left:505px">Stridewear</div>
<div class="client-logo" style="left:716px">GOLDMERE</div>
<div class="client-logo" style="left:932px">movewise.com</div>

<footer class="site-footer" role="contentinfo">
  <div class="footer-col" style="left:79px">
    <h4>Get in Touch</h4>
    <ul>
      <li>&gt;&nbsp; Head Office</li>
      <li class="addr">2150 Harbor Ave<br>Suite 310<br>Lakeview, NJ 07450<br>Phone: +1 (555) 014 2286 <span>FREE</span></li>
      <li>&gt;&nbsp; Technical Center</li>
      <li>&gt;&nbsp; West Cost Office</li>
    </ul>
  </div>
  <div class="footer-col" style="left:345px">
    <h4>About</h4>
    <ul><li>Company</li><li>Services</li><li>Solution</li><li>Resources</li><li>Career</li><li>Contact Us</li></ul>
  </div>
  <div class="footer-col" style="left:608px">
    <h4>Follow Us</h4>
    <div class="social"><i><b></b></i><i><b></b></i><i><b></b></i></div>
  </div>
  <div class="footer-col newsletter" style="left:876px">
    <h4>Join Our Newsletter</h4>
    <p>And always stay informed of the latest company news and events !</p>
    <div class="email-field">Email*</div>
    <div class="subscribe">Subscribe</div>
  </div>
</footer>
<div class="copyright">&copy; 2016. <span>BEACON ADVISORY</span>. All Rights Reserved.</div>

</body>
</html>
```